Dietitian needs awesome business card

I need a contemporary design that's eye catching but professional.
My card is to given to doctors, specialists and patients alike.
I manage patients with chronic diseases
I have uploaded my logo and current business card, I would also like the other Certified Clinical Nutritionist logo incorporated into the design

Target Market(s)

Doctors, specialists and patients

Industry/Entity Type

Healthcare

Contact Information for Business Card

www.brightfieldnutrition.com.au
Ph: 0427 561 903
Fax: 6457 2183
email: marcus.k.diet@fernmail.com
Space on the back of the card with: Appointment date, Appointment time and appointment location

Font styles to use
Serif

Colors
fbee3e
876aae
ffc214

Requirements
Must have
• My Logo
• Certified Clinical Nutritionist Logo
• My 4 locations - Pinebrook Medical Centre, North Corrin Health, Hollis Medical, Ashcombe Doctors Surgery
Nice to have
• I like the colours in my current business card

```html
<!DOCTYPE html>
<html lang="en">
<head>
<meta charset="utf-8">
<title>Brightfield Nutrition & Dietetics – Business Card</title>
<link rel="stylesheet" href="https://fonts.googleapis.com/css2?family=Philosopher:wght@400;700&family=Open+Sans:wght@400&display=swap">
<style>
  :root {
    --page-bg: #ececec;
    --card-bg: #ffffff;
    --navy: #1f3a93;
    --deep-navy: #1e2a78;
    --bright-blue: #0a82d0;
    --leaf-green: #7dbb2a;
    --text-grey: #444a55;
    --divider: #c9ccd2;
    --badge-orange: #f47a2a;
  }
  * { box-sizing: border-box; margin: 0; padding: 0; }
  html, body {
    width: 1105px; height: 1200px; overflow: hidden;
    background: var(--page-bg);
  }
  .card {
    position: absolute; left: 179px;
    width: 747px; height: 424px;
    background: var(--card-bg);
    overflow: hidden;
  }
  .card--front { top: 120px; }
  .card--back { top: 640px; }

  /* Front */
  .brand {
    position: absolute; left: 48px; top: 180px;
    display: flex; align-items: center; gap: 14px;
  }
  .brand__dot {
    width: 54px; height: 54px; border-radius: 50%;
    background: var(--leaf-green);
  }
  .brand__name {
    font-family: "Philosopher", serif; font-weight: 400;
    color: var(--navy); font-size: 22px; line-height: 1.2;
  }
  .divider {
    position: absolute; left: 353px; top: 115px;
    width: 2px; height: 193px; background: var(--divider);
  }
  .person { position: absolute; left: 382px; top: 112px; font-family: "Philosopher", serif; }
  .person__name { color: var(--navy); font-size: 28px; line-height: 1.1; }
  .person__role { color: var(--leaf-green); font-size: 20px; margin-top: 6px; }
  .contacts {
    position: absolute; left: 382px; top: 192px; list-style: none;
    font-family: "Philosopher", serif; font-size: 20.5px; color: var(--text-grey);
  }
  .contacts li { display: flex; align-items: center; gap: 10px; height: 28.7px; }
  .contacts svg { width: 18px; height: 18px; fill: var(--navy); flex: none; }
  .accent-line {
    position: absolute; left: 0; right: 0; top: 389px; height: 3px;
    background: var(--leaf-green);
  }
  .accent-band {
    position: absolute; left: 0; right: 0; top: 394px; bottom: 0;
    background: linear-gradient(90deg, var(--deep-navy) 0%, var(--bright-blue) 50%, var(--deep-navy) 100%);
  }

  /* Back */
  .watermark-art {
    position: absolute; left: 0; top: 14px; width: 355px; height: 410px;
    background: radial-gradient(ellipse at 45% 55%, #e6eef8 0%, #eef5e4 55%, rgba(255,255,255,0) 75%);
  }
  .cert-badge {
    position: absolute; left: 382px; top: 50px; width: 178px; height: 84px;
    background: var(--badge-orange); border-radius: 3px;
  }
  .cert-badge__seal {
    position: absolute; right: 18px; top: 12px; width: 60px; height: 60px;
    border-radius: 50%; background: #ffffff;
  }
  .appointment {
    position: absolute; left: 382px; font-family: "Open Sans", sans-serif;
    color: var(--navy); font-size: 20.5px; display: flex; align-items: baseline; gap: 4px;
  }
  .appointment--date { top: 170px; }
  .appointment--time { top: 216px; }
  .appointment__fill { border-bottom: 2px dotted var(--navy); display: inline-block; transform: translateY(-4px); }
  .appointment--date .appointment__fill { width: 212px; }
  .appointment--time .appointment__fill { width: 150px; }
  .appointment__suffix { font-size: 16px; margin-left: 6px; }
  .locations {
    position: absolute; left: 382px; top: 284px; list-style: none;
    font-family: "Open Sans", sans-serif; font-size: 20px; color: var(--text-grey);
  }
  .locations li { display: flex; align-items: center; gap: 14px; height: 27px; }
  .locations__box { width: 16px; height: 16px; border: 2px solid var(--navy); flex: none; }
</style>
</head>
<body>
  <section class="card card--front">
    <div class="brand">
      <div class="brand__dot"></div>
      <div class="brand__name">Brightfield<br>Nutrition &amp; Dietetics</div>
    </div>
    <div class="divider"></div>
    <div class="person">
      <h1 class="person__name" style="font-weight:400">Marcus Kendrick</h1>
      <p class="person__role">Nutritionist &amp; Chef</p>
    </div>
    <ul class="contacts">
      <li><svg viewBox="0 0 24 24"><path d="M6.6 10.8a15.1 15.1 0 0 0 6.6 6.6l2.2-2.2a1 1 0 0 1 1-.25 11.4 11.4 0 0 0 3.6.57 1 1 0 0 1 1 1V20a1 1 0 0 1-1 1A17 17 0 0 1 3 4a1 1 0 0 1 1-1h3.5a1 1 0 0 1 1 1c0 1.25.2 2.45.57 3.57a1 1 0 0 1-.25 1z"/></svg>0427 561 903</li>
      <li><svg viewBox="0 0 24 24"><path d="M6 2h10l2 2v5H6zM3 10h18a1 1 0 0 1 1 1v7h-4v4H6v-4H2v-7a1 1 0 0 1 1-1zm5 6v4h8v-4z"/></svg>6457 2183</li>
      <li><svg viewBox="0 0 24 24"><path d="M2 5h20v14H2zm2 2v.5l8 5 8-5V7z"/></svg>marcus.k.diet@fernmail.com</li>
      <li><svg viewBox="0 0 24 24"><circle cx="12" cy="12" r="10"/><path d="M2 12h20M12 2c3 3 3 17 0 20M12 2c-3 3-3 17 0 20" stroke="#fff" stroke-width="1.4" fill="none"/></svg>brightfieldnutrition.com.au</li>
    </ul>
    <div class="accent-line"></div>
    <div class="accent-band"></div>
  </section>

  <section class="card card--back">
    <div class="watermark-art" role="img" aria-label="Faint enlarged brand symbol decoration"></div>
    <div class="cert-badge" role="img" aria-label="Certified Clinical Nutritionist badge"><div class="cert-badge__seal"></div></div>
    <p class="appointment appointment--date">Date :<span class="appointment__fill"></span></p>
    <p class="appointment appointment--time">Time :<span class="appointment__fill"></span><span class="appointment__suffix">AM/PM</span></p>
    <ul class="locations">
      <li><span class="locations__box"></span>Pinebrook Medical Centre</li>
      <li><span class="locations__box"></span>North Corrin Health</li>
      <li><span class="locations__box"></span>Hollis Medical</li>
      <li><span class="locations__box"></span>Ashcombe Doctors Surgery</li>
    </ul>
  </section>
</body>
</html>
```